Letterhead for a German Distribution/Manufacturing Company

We need a professional Letterhead in a unique Design.
not to playful.
The Letterhead has to show show that we are a international company with headquater in Germany.
all details like adress, Vat Tax Number, Bank Accout, Eori, email, Company number has to be on the Letterhead.
for example use: VAT TAX DE5470318 Bank Account: Kestrel Bank IBAN DE412058731ß204683 Swift: MORV0417352 EORI 3150428697 Company Number: HRB 51806 Adress: VOLMINTA UG Ahornweg 7 Postal Code 06384 City Wendelsbach Country: Germany Email: info@volminta-example.com
the design can be colored but doesnt have to be
Industry/Entity Type
Manufacturing and international distribution
Requirements
Must have
- show that we are a international company with headquater in Germany. our company infos and logo

```html
<!DOCTYPE html>
<html lang="en">
<head>
<meta charset="utf-8">
<title>Volminta Letterhead</title>
<link href="https://fonts.googleapis.com/css2?family=Arimo:wght@400;700&family=Questrial&display=swap" rel="stylesheet">
<style>
  :root {
    --backdrop: #cbcacb;
    --paper: #ffffff;
    --ink: #4a4a4a;
    --ink-soft: #555555;
    --band: #484848;
  }
  * { margin: 0; padding: 0; box-sizing: border-box; }
  html, body {
    width: 1173px; height: 1200px; overflow: hidden;
    background: var(--backdrop);
  }
  .sheet {
    position: absolute; left: 230px; top: 96px;
    width: 714px; height: 1009px;
    background: var(--paper);
    overflow: hidden;
    font-family: "Arimo", Arial, sans-serif;
    color: var(--ink-soft);
  }
  .brand {
    position: absolute; left: 44px; top: 68px;
    display: flex; align-items: center; gap: 12px;
    font-family: "Questrial", sans-serif;
    font-size: 38px; letter-spacing: 1px;
    color: var(--ink);
  }
  .brand-dot {
    width: 40px; height: 40px; border-radius: 50%;
    background: var(--ink);
  }
  .company-facts {
    position: absolute; right: 190px; top: 44px;
    text-align: right; font-size: 11.2px; line-height: 14.2px;
    white-space: nowrap;
  }
  .company-facts b { color: var(--ink); }
  .header-divider {
    position: absolute; left: 538px; top: 47px;
    width: 1px; height: 83px; background: var(--ink);
  }
  .contact {
    position: absolute; left: 552px; top: 42px;
    font-size: 11.2px; line-height: 14.2px;
    white-space: nowrap;
  }
  .contact-line { display: flex; align-items: center; gap: 7px; }
  .contact-line svg { width: 9px; height: 9px; fill: var(--ink); flex: none; }
  .salutation {
    position: absolute; left: 65px; top: 309px;
    font-family: "Questrial", sans-serif; font-weight: 400;
    font-size: 16.5px; color: var(--ink);
    -webkit-text-stroke: 0.3px var(--ink);
  }
  .letter-body {
    position: absolute; left: 64px; top: 357px;
    font-size: 11.6px; line-height: 14.7px;
    white-space: nowrap;
  }
  .letter-body p { margin-bottom: 12.7px; }
  .closing {
    position: absolute; left: 65px; top: 660px;
    font-family: "Questrial", sans-serif; font-size: 9px; font-weight: 400;
    color: var(--ink); -webkit-text-stroke: 0.3px var(--ink);
  }
  .signature {
    position: absolute; left: 64px; top: 705px;
    width: 117px; height: 32px;
    background: linear-gradient(90deg, #e9e9e9, #dadada);
    border-radius: 3px;
  }
  .footer-rule {
    position: absolute; left: 0; right: 0; bottom: 62px;
    height: 3px; background: var(--band);
  }
  .footer-band {
    position: absolute; left: 0; right: 0; bottom: 0;
    height: 54px; background: var(--band);
  }
</style>
</head>
<body>
  <div class="sheet">
    <header>
      <div class="brand"><span class="brand-dot"></span>VOLMINTA</div>
      <div class="company-facts">
        <div><b>VAT TAX</b> DE5470318</div>
        <div><b>Bank Account:</b> Kestrel Bank</div>
        <div><b>IBAN</b> DE412058731ß204683</div>
        <div><b>Swift:</b> MORV0417352</div>
        <div><b>EORI</b> 3150428697</div>
        <div><b>Company Number:</b> HRB 51806</div>
      </div>
      <div class="header-divider"></div>
      <div class="contact">
        <div>Ahornweg 7</div>
        <div>06384, Wendelsbach</div>
        <div>Germany</div>
        <div class="contact-line" style="margin-top:2px">
          <svg viewBox="0 0 10 10"><path d="M2 0.5 L3.6 2.6 L2.7 3.6 C3.3 5 4.9 6.6 6.3 7.2 L7.3 6.3 L9.5 7.9 L8.3 9.5 C4.5 9.2 0.8 5.5 0.5 1.7Z"/></svg>555-014-2890
        </div>
        <div class="contact-line">
          <svg viewBox="0 0 10 10"><path d="M0.5 2 H9.5 V8 H0.5Z M1 2.4 L5 5.5 L9 2.4" stroke="#fff" stroke-width="0.8"/></svg>info@volminta-example.com
        </div>
        <div class="contact-line">
          <svg viewBox="0 0 10 10"><circle cx="5" cy="5" r="4.5"/><path d="M0.5 5 H9.5 M5 0.5 C3 3 3 7 5 9.5 M5 0.5 C7 3 7 7 5 9.5" stroke="#fff" stroke-width="0.7" fill="none"/></svg>www.volminta.example
        </div>
      </div>
    </header>

    <h1 class="salutation">Dear Mr. Hartley,</h1>

    <main class="letter-body">
      <p>Lorem ipsum dolor sit amet, consectetuer adipiscing elit, sed diam nonmmy nibh euismod tincidunt ut laor<br>eet dolore magna aliquam erat volutpat. Ut wisi enim ad minim veniam, quis nostrud exerci tationmcorper<br>suscipit lobortis nisl ut aliquip ex ea commodo consequat. Duis autem vel eum iriure dolor in hendrerit in<br>vulputate velit esse molestie consequat, vel illum dolore eu feugiat</p>
      <p>Rorem ipsum dolor sit amet, consectetuer adipiscing elit, sed diam nonmmy nibh euismod tincidunt ut laor<br>eet dolore magna aliquam erat volutpat. Ut wisi enim ad minim veniam, quis nostrud exerci tationmcorper<br>suscipit lobortis nisl ut aliquip ex ea commodo consequat. Duis autem vel eum iriure dolor in hendrerit in<br>vulputate velit esse molest</p>
      <p>Dorem ipsum dolor sit amet, consectetuer adipiscing elit, sed diam nonmmy nibh euismod tincidunt ut laor<br>eet dolore magna aliquam erat volutpat. Ut wisi enim ad minim veniam, quis nostrud exerci tationmcorper<br>suscipit lobortis nisl ut aliquip ex ea commodo consequat. Duis autem vel eum iriure dolor in hendrerit in<br>suscipit lobortis nisl ut aliquip ex ea commodo consequat. Duis autem vel eum iriure dolor in hendrerit in<br>vulputate velit esse molestie consequat, vel illum</p>
      <p>Sorem ipsum dolor sit amet, consectetuer adipiscing elit, sed diam nonmmy nibh euismod tincidunt ut laor<br>eet dolore magna aliquam erat volutpat. Ut wisi enim ad minim veniam, quis nostrud exerci tationmcorper<br>suscipit lobortis nisl ut aliquip ex ea commodo consequat. Duis autem vel eum iriure dolor in</p>
    </main>

    <div class="closing">Sincerely,</div>
    <div class="signature" role="img" aria-label="Handwritten signature of the sender"></div>

    <footer>
      <div class="footer-rule"></div>
      <div class="footer-band"></div>
    </footer>
  </div>
</body>
</html>
```